Business Card for beauty technology startup

Design Glimora Business Card for a Beauty, based on the website identity and colors (https://www.glimora-example.com).
Glimora is a beauty tech startup that gathers helpful product info for beauty lovers and consumers (such as availability on stores, price range and product reviews) for makeup products. The card design must be young, colorful but clean, and very modern.

Target Market(s)

woman, 15-35

Industry/Entity Type

Cosmetics

Contact Information for Business Card

Full Name, address, phone

Font styles to use
Other font styles liked:
• Advent Pro

Colors
e34297
86cfc6
ffffff
5c5c5c
e8e8e8
e667a6
b2b2b2

Requirements
Must have
• One full colored side with a creative design and another with card info
• Use Color palette: #95C5C5 and/or #D38AA5
• Use fonts: Advent Pro
• Use website identity: https://www.glimora-example.com
Nice to have
• If needed extra font: Roboto

```html
<!DOCTYPE html>
<html lang="en">
<head>
<meta charset="utf-8">
<title>Glimora Business Card</title>
<link rel="stylesheet" href="https://fonts.googleapis.com/css2?family=Advent+Pro:wght@200;300;400&family=Roboto:wght@400;500&family=Roboto+Condensed:wght@700&display=swap">
<style>
  :root {
    --stage: #5b5a58;
    --card-dark: #1e1e20;
    --rose: #c17f99;
    --rose-card: #c28198;
    --rose-light: #f2b3cf;
    --white: #ffffff;
  }
  * { box-sizing: border-box; margin: 0; padding: 0; }
  html, body {
    width: 1200px; height: 960px; overflow: hidden;
    background: var(--stage);
  }
  .canvas { position: relative; width: 1200px; height: 960px; }

  .card {
    position: absolute;
    border-radius: 18px;
    overflow: hidden;
    box-shadow: 0 4px 10px rgba(0,0,0,0.35);
  }

  /* Front side */
  .card-front {
    left: 315px; top: 113px; width: 598px; height: 344px;
    background: var(--card-dark);
    color: var(--white);
  }
  .brand-row {
    position: absolute; left: 27px; top: 32px;
    display: flex; align-items: center; gap: 28px;
  }
  .brand-dot {
    width: 66px; height: 66px; border-radius: 50%;
    border: 3px solid var(--rose);
  }
  .brand-name {
    font-family: "Advent Pro", sans-serif;
    font-weight: 300;
    font-size: 46px;
    letter-spacing: 6px;
    color: var(--rose);
    line-height: 1;
  }
  .decor-ring {
    position: absolute; left: 312px; top: 37px;
    width: 266px; height: 266px; border-radius: 50%;
    border: 4px solid var(--rose);
  }
  .holder {
    position: absolute; left: 26px; top: 123px;
    font-family: "Roboto", sans-serif;
  }
  .holder-name {
    font-family: "Roboto Condensed", sans-serif;
    font-weight: 700; font-size: 19px;
    color: var(--rose); letter-spacing: 0.3px;
  }
  .holder-title { font-weight: 500; font-size: 14px; margin-top: 3px; }
  .address { margin-top: 13px; font-size: 14px; line-height: 19px; }
  .contacts { list-style: none; margin-top: 10px; font-size: 14px; }
  .contacts li {
    display: flex; align-items: center; gap: 9px; height: 19px;
  }
  .contacts svg { width: 14px; height: 14px; fill: var(--rose); flex: none; }

  /* Back side */
  .card-back {
    left: 311px; top: 472px; width: 600px; height: 341px;
    background: var(--rose-card);
    text-align: center;
  }
  .back-dot {
    position: absolute; left: 251px; top: 78px;
    width: 100px; height: 100px; border-radius: 50%;
    border: 3px solid var(--rose-light);
  }
  .back-name {
    position: absolute; left: 0; right: 0; top: 210px;
    font-family: "Advent Pro", sans-serif;
    font-weight: 300; font-size: 46px; letter-spacing: 6px;
    color: var(--rose-light); line-height: 1;
  }
  .back-url {
    position: absolute; left: 0; right: 0; top: 294px;
    font-family: "Roboto", sans-serif;
    font-size: 13px; letter-spacing: 4px;
    color: var(--rose-light);
  }
</style>
</head>
<body>
<main class="canvas">
  <section class="card card-front">
    <div class="brand-row">
      <span class="brand-dot"></span>
      <span class="brand-name">GLIMORA</span>
    </div>
    <span class="decor-ring"></span>

    <div class="holder">
      <p class="holder-name">CLARA NOVAK</p>
      <p class="holder-title">CEO/FOUNDER</p>
      <p class="address">4120 Willow Crest Road<br>Juneau, Alaska 99801</p>
      <ul class="contacts">
        <li>
          <svg viewBox="0 0 24 24" aria-hidden="true"><path d="M6.6 10.8a15.1 15.1 0 0 0 6.6 6.6l2.2-2.2c.3-.3.7-.4 1-.2 1.1.4 2.3.6 3.6.6.6 0 1 .4 1 1V20c0 .6-.4 1-1 1A17 17 0 0 1 3 4c0-.6.4-1 1-1h3.5c.6 0 1 .4 1 1 0 1.3.2 2.5.6 3.6.1.3 0 .7-.2 1z"/></svg>
          <span>555 214 7730</span>
        </li>
        <li>
          <svg viewBox="0 0 24 24" aria-hidden="true"><path d="M7 1h10a2 2 0 0 1 2 2v18a2 2 0 0 1-2 2H7a2 2 0 0 1-2-2V3a2 2 0 0 1 2-2zm0 3v14h10V4zm5 15.5a1 1 0 1 0 0 2 1 1 0 0 0 0-2z"/></svg>
          <span>555 309 4418</span>
        </li>
        <li>
          <svg viewBox="0 0 24 24" aria-hidden="true"><path d="M6 2h12v6H6zM3 9h18a2 2 0 0 1 2 2v7h-4v4H5v-4H1v-7a2 2 0 0 1 2-2zm4 8v3h10v-3z"/></svg>
          <span>555 672 0159</span>
        </li>
        <li>
          <svg viewBox="0 0 24 24" aria-hidden="true"><path d="M2 5h20v14H2zm2 2v.5l8 5 8-5V7zm0 2.9V17h16V9.9l-8 5z"/></svg>
          <span>info@glimora-example.com</span>
        </li>
        <li>
          <svg viewBox="0 0 24 24" aria-hidden="true"><path d="M12 2a10 10 0 1 0 0 20 10 10 0 0 0 0-20zm-1 17.9A8 8 0 0 1 4.2 10.2L9 15v1a2 2 0 0 0 2 2zm6.9-2.5A2 2 0 0 0 16 16h-1v-3a1 1 0 0 0-1-1H8v-2h2a1 1 0 0 0 1-1V7h2a2 2 0 0 0 2-2v-.4a8 8 0 0 1 2.9 12.8z"/></svg>
          <span>www.glimora-example.com</span>
        </li>
      </ul>
    </div>
  </section>

  <section class="card card-back">
    <span class="back-dot"></span>
    <p class="back-name">GLIMORA</p>
    <p class="back-url">www.glimora-example.com</p>
  </section>
</main>
</body>
</html>
```